A weight loss and fitness website design

I am into different types of modern weight loss techniques for people who are a little fatty and wish to be physically and mentally fit. Basically, the website is to teach people how to reduce weight using different methods such as diet, exercises, yoga and other forms. I would need an eye catching website which would make visitors want to come back. The will be also be different forms of exercises for a health and fit life. This said, my website is to have two categories of
1) weight loss techniques
2) exercise of fit and healthy living.
I prefer bright colors such as green, blue, yellow, and orange. Imagery should include before and after pictures of people suffering from obesity, people under going exercises.
Designers can get ideas and inspiration from the website fitlumen.com which i was previously part of the team.
Target Market(s)
My target audience are people suffering from obesity, malnutrition and physical deficiency.
Industry/Entity Type
Fitness
Coding
Coded - Design and coding required
Number of Pages Required
1 page
Look and feel

```html
<!DOCTYPE html>
<html lang="en">
<head>
<meta charset="utf-8">
<title>Verdell Fitness</title>
<link rel="stylesheet" href="https://fonts.googleapis.com/css2?family=Open+Sans:wght@400;600&family=Raleway:wght@300;400;500&display=swap">
<style>
:root{
  --blue:#3a8fd8;
  --sky:#5ab4f3;
  --orange:#ff8a00;
  --green:#6cbf2a;
  --green-dark:#4e9a18;
  --ink:#2b2b2b;
  --text:#666;
  --muted:#8a8a8a;
  --band:#ececec;
  --line:#dcdcdc;
  --white:#fff;
  --dark-bar:#4a4a4a;
}
*{box-sizing:border-box;margin:0;padding:0}
html,body{width:1200px;height:2632px;overflow:hidden}
body{position:relative;background:var(--white);font-family:"Open Sans",Arial,sans-serif;color:var(--text)}
.abs{position:absolute}
.heading{font-family:"Raleway",Arial,sans-serif;font-weight:400}

/* header */
.site-header{position:absolute;left:0;top:0;width:1200px;height:96px;border-bottom:1px solid var(--line);background:var(--white)}
.brand{position:absolute;left:119px;top:24px;font-family:"Raleway",Arial,sans-serif;font-size:33px;font-weight:400;color:var(--blue);line-height:1}
.main-nav a{position:absolute;top:38px;font-family:"Raleway",Arial,sans-serif;font-size:17px;color:var(--ink);text-decoration:none;line-height:1}
.main-nav a.active{color:var(--orange)}

/* hero */
.hero{position:absolute;left:0;top:96px;width:1200px;height:492px;background:linear-gradient(90deg,#f3f4f6 0%,#e6e9ed 100%);overflow:hidden;border-bottom:1px solid var(--line)}
.hero-photo{position:absolute;left:300px;top:0;width:780px;height:492px;background:radial-gradient(ellipse at 60% 55%,#5f8fc7 0%,#9fb6cf 30%,rgba(230,233,237,0) 65%)}
.hero-title{position:absolute;left:126px;top:128px;font-size:44px;color:var(--blue);line-height:1;letter-spacing:.5px}
.hero-sub{position:absolute;left:126px;top:189px;font-size:33px;color:var(--ink);line-height:1}
.hero-text{position:absolute;left:126px;top:236px;width:380px;font-size:13px;line-height:21px;color:var(--muted)}
.btn-blue{position:absolute;left:126px;top:293px;width:116px;height:34px;background:var(--blue);color:var(--white);font-size:14px;line-height:34px;text-align:center}
.hero-dots{position:absolute;left:568px;top:461px;display:flex;gap:3px}
.hero-dots span{width:13px;height:13px;border-radius:50%;background:#666}
.hero-dots span.off{background:var(--white);border:2px solid #666}

/* about */
.about-photo{position:absolute;left:175px;top:605px;width:290px;height:393px;background:linear-gradient(180deg,#f0c9b0 0%,#e98a70 45%,#3d3a5a 100%);border-radius:140px 140px 0 0}
.about-title{position:absolute;left:523px;top:660px;font-size:33px;color:var(--ink);line-height:1}
.about-lead{position:absolute;left:523px;top:709px;font-size:20px;color:var(--text);line-height:1}
.about-text{position:absolute;left:523px;top:752px;width:540px;font-size:13px;line-height:28px;color:var(--text)}
.btn-green{position:absolute;left:526px;top:882px;width:125px;height:36px;background:linear-gradient(180deg,var(--green),var(--green-dark));color:var(--white);font-size:12px;line-height:36px;text-align:center;border-radius:3px;letter-spacing:.3px}

/* features */
.features{position:absolute;left:0;top:998px;width:1200px;height:351px;background:var(--band)}
.feature{position:absolute;top:64px;width:260px;text-align:center}
.feature-icon{width:106px;height:106px;margin:0 auto;border-radius:50%;background:var(--white);display:flex;align-items:center;justify-content:center}
.feature-title{margin-top:24px;font-family:"Raleway",Arial,sans-serif;font-size:19px;color:var(--ink);line-height:1}
.feature-text{margin-top:13px;font-size:12.5px;line-height:21px;color:var(--muted)}

/* category panels */
.panel{position:absolute;left:0;width:1200px;overflow:hidden}
.panel-photo{position:absolute;top:0;height:100%}
.panel-title{position:absolute;font-size:30px;color:var(--white);line-height:1}
.panel-text{position:absolute;width:430px;font-size:13.5px;line-height:22px;color:var(--white)}
.panel-text.small{font-size:12px;line-height:21px}
.btn-outline{position:absolute;height:40px;border:2px solid var(--white);color:var(--white);font-size:14px;line-height:36px;text-align:center}

/* gallery */
.gallery-title{position:absolute;left:0;top:2204px;width:1200px;text-align:center;font-size:25px;color:var(--blue);line-height:1}
.gallery-card{position:absolute;top:2260px;width:232px;height:140px;border:1px solid #cfcfcf;display:flex}
.gallery-shot{position:relative;flex:1;border-right:1px solid #e2e2e2}
.gallery-shot:last-child{border-right:none}
.gallery-shot .pic{position:absolute;left:0;top:0;right:0;bottom:21px}
.gallery-shot .label{position:absolute;left:0;right:0;bottom:0;height:21px;background:var(--dark-bar);color:var(--white);font-size:10px;line-height:21px;text-align:center;letter-spacing:.5px}
.gallery-arrow{position:absolute;top:2313px}

/* footer */
.site-footer{position:absolute;left:0;top:2495px;width:1200px;height:137px;background:var(--band)}
.footer-nav a{position:absolute;top:29px;font-family:"Raleway",Arial,sans-serif;font-size:16px;color:var(--ink);text-decoration:none;line-height:1}
.copyright{position:absolute;left:128px;top:58px;font-size:12px;color:var(--text)}
.social{position:absolute;top:36px;width:32px;height:32px;border-radius:50%;background:var(--blue)}
</style>
</head>
<body>

<header class="site-header">
  <div class="brand">Verdell Fitness</div>
  <nav class="main-nav">
    <a class="active" style="left:483px">Home</a>
    <a style="left:572px">About Us</a>
    <a style="left:681px">Services</a>
    <a style="left:782px">Training</a>
    <a style="left:881px">Join</a>
    <a style="left:947px">Contact</a>
  </nav>
</header>

<section class="hero">
  <div class="hero-photo" role="img" aria-label="Athletic man doing a sit-up crunch in a blue tank top"></div>
  <h1 class="hero-title heading">MODERN WEIGHT</h1>
  <div class="hero-sub heading">LOSS TECHNIQUES</div>
  <p class="hero-text">Cras a ante vitae enim iaculis aliquam Mauris nunc quam venenatis nec euismod sit amet egestas</p>
  <div class="btn-blue">Start Now</div>
  <div class="hero-dots"><span class="off"></span><span></span><span></span><span></span></div>
</section>

<section class="about">
  <div class="about-photo" role="img" aria-label="Slim woman in sportswear measuring her waist with a tape"></div>
  <h2 class="about-title heading">About Verdell Fitness</h2>
  <div class="about-lead heading">Nam cursus Morbi ut mi Nullam enim leo egestas</div>
  <p class="about-text">magnis dis parturient montes nascetur ridiculus mus In iaculis facilisis massa Etiam eu urna Sed porta Suspendisse quam leo molestie sed luctus quis feugiat in pede Fusce tellus Sed metus augue convallis et vehicula ut pulvinar eu ante Integer orci tellus tristique vitae consequat nec porta vel lectus Nulla sit amet diam</p>
  <div class="btn-green">READ MORE</div>
</section>

<section class="features">
  <div class="feature" style="left:159px">
    <div class="feature-icon">
      <svg width="52" height="52" viewBox="0 0 52 52" fill="none" stroke="#6cbf2a" stroke-width="2.2" stroke-linecap="round" stroke-linejoin="round" aria-hidden="true">
        <path d="M26 16c-4-3-13-3-15 6-2 10 5 24 11 24 2 0 3-1 4-1s2 1 4 1c6 0 13-14 11-24-2-9-11-9-15-6z"/>
        <path d="M26 16c0-5 2-8 5-10"/>
        <path d="M27 12c3-4 8-4 10-3-2 3-6 4-10 3z"/>
      </svg>
    </div>
    <div class="feature-title">Healthy Diet</div>
    <p class="feature-text">molestie sed luctus quis feugiat in pede Fusce tellus Sed metus augue convallis et vehicula ut pulvinar</p>
  </div>
  <div class="feature" style="left:470px">
    <div class="feature-icon">
      <svg width="56" height="56" viewBox="0 0 56 56" fill="none" stroke="#6cbf2a" stroke-width="2.2" stroke-linecap="round" stroke-linejoin="round" aria-hidden="true">
        <rect x="8" y="10" width="26" height="34" rx="2"/>
        <rect x="15" y="6" width="12" height="7" rx="1.5"/>
        <path d="M13 21l3 3 5-6M13 32l3 3 5-6"/>
        <circle cx="38" cy="38" r="11" fill="#fff"/>
        <path d="M38 32v6l4 3M36 24h4"/>
      </svg>
    </div>
    <div class="feature-title">Excercise &amp; &nbsp;Fitness</div>
    <p class="feature-text">molestie sed luctus quis feugiat in pede Fusce tellus Sed metus augue convallis et vehicula ut pulvinar</p>
  </div>
  <div class="feature" style="left:779px">
    <div class="feature-icon">
      <svg width="56" height="56" viewBox="0 0 56 56" fill="none" stroke="#6cbf2a" stroke-width="2.2" stroke-linecap="round" stroke-linejoin="round" aria-hidden="true">
        <path d="M28 12c-5 6-5 14 0 22 5-8 5-16 0-22z"/>
        <path d="M28 34c-6-2-12-8-14-15 7 1 12 6 14 15z"/>
        <path d="M28 34c6-2 12-8 14-15-7 1-12 6-14 15z"/>
        <path d="M10 42h36"/>
      </svg>
    </div>
    <div class="feature-title">Yoga &amp; Other</div>
    <p class="feature-text">molestie sed luctus quis feugiat in pede Fusce tellus Sed metus augue convallis et vehicula ut pulvinar</p>
  </div>
</section>

<section class="panel weight-loss" style="top:1349px;height:388px;background:var(--orange)">
  <div class="panel-photo" role="img" aria-label="Woman lifting a loaded barbell onto her shoulders in a gym" style="left:580px;width:620px;background:linear-gradient(135deg,#d9dde0 0%,#9aa2a8 45%,#3a3a3a 100%)"></div>
  <svg class="abs" style="left:0;top:0" width="1200" height="388" viewBox="0 0 1200 388" aria-hidden="true">
    <path d="M0 0H690C630 20 600 90 598 190C596 290 610 360 600 388H0Z" fill="#ff8a00"/>
  </svg>
  <h2 class="panel-title heading" style="left:142px;top:79px">Weight Loss Techniques</h2>
  <p class="panel-text" style="left:145px;top:125px">Cras a ante vitae enim iaculis aliquam Mauris nunc quam venenatis nec euismod sit amet egestas placerat</p>
  <p class="panel-text small" style="left:145px;top:180px">habitant morbi tristique senectus et netus et malesuada fames ac turpis egestas Cras id elit Integer quis urna Ut ante enim dapibus malesuada fringilla eu condimentum quis tellus Aenean porttitor eros</p>
  <div class="btn-outline" style="left:146px;top:272px;width:136px">Learn More</div>
</section>

<section class="panel healthy-living" style="top:1737px;height:403px;background:var(--sky)">
  <div class="panel-photo" role="img" aria-label="Man doing a one-arm plank exercise in a training hall" style="left:0;width:720px;background:linear-gradient(135deg,#c9ced2 0%,#8e969c 50%,#4a4f54 100%)"></div>
  <svg class="abs" style="left:0;top:0" width="1200" height="403" viewBox="0 0 1200 403" aria-hidden="true">
    <path d="M1200 0H575C640 40 700 110 700 200C700 300 690 360 700 403H1200Z" fill="#5ab4f3"/>
  </svg>
  <h2 class="panel-title heading" style="left:668px;top:91px">Exercise of fit and healthy living</h2>
  <p class="panel-text" style="left:668px;top:135px">Cras a ante vitae enim iaculis aliquam Mauris nunc quam venenatis nec euismod sit amet egestas placerat</p>
  <p class="panel-text small" style="left:668px;top:190px">habitant morbi tristique senectus et netus et malesuada fames ac turpis egestas Cras id elit Integer quis urna Ut ante enim dapibus malesuada fringilla eu condimentum quis tellus Aenean porttitor eros</p>
  <div class="btn-outline" style="left:672px;top:267px;width:133px">Learn More</div>
</section>

<section class="gallery">
  <h2 class="gallery-title heading">Before &amp; After Gallery</h2>
  <svg class="gallery-arrow" style="left:92px" width="16" height="26" viewBox="0 0 16 26" aria-hidden="true"><path d="M13 2L3 13l10 11" fill="none" stroke="#999" stroke-width="2.5"/></svg>
  <div class="gallery-card" style="left:121px">
    <div class="gallery-shot"><div class="pic" role="img" aria-label="Woman before weight loss" style="background:linear-gradient(180deg,#f3f3f3,#d8d8d8)"></div><div class="label">BEFORE</div></div>
    <div class="gallery-shot"><div class="pic" role="img" aria-label="Same woman after weight loss" style="background:linear-gradient(180deg,#f3f3f3,#dcdcdc)"></div><div class="label">AFTER</div></div>
  </div>
  <div class="gallery-card" style="left:365px">
    <div class="gallery-shot"><div class="pic" role="img" aria-label="Woman in green top before weight loss" style="background:linear-gradient(180deg,#eef2ea,#a9c98f)"></div><div class="label">BEFORE</div></div>
    <div class="gallery-shot"><div class="pic" role="img" aria-label="Woman in green top after weight loss" style="background:linear-gradient(180deg,#eef2ea,#b6d39c)"></div><div class="label">AFTER</div></div>
  </div>
  <div class="gallery-card" style="left:605px">
    <div class="gallery-shot"><div class="pic" role="img" aria-label="Blonde woman before toning" style="background:linear-gradient(180deg,#f6efe6,#d9b9a0)"></div><div class="label">BEFORE</div></div>
    <div class="gallery-shot"><div class="pic" role="img" aria-label="Blonde woman after toning" style="background:linear-gradient(180deg,#f6efe6,#d6b49a)"></div><div class="label">AFTER</div></div>
  </div>
  <div class="gallery-card" style="left:847px">
    <div class="gallery-shot"><div class="pic" role="img" aria-label="Torso in black sportswear before" style="background:linear-gradient(180deg,#f2ebe6,#5a5252)"></div><div class="label">BEFORE</div></div>
    <div class="gallery-shot"><div class="pic" role="img" aria-label="Torso in black sportswear after" style="background:linear-gradient(180deg,#f2ebe6,#4f4747)"></div><div class="label">AFTER</div></div>
  </div>
  <svg class="gallery-arrow" style="left:1087px" width="16" height="26" viewBox="0 0 16 26" aria-hidden="true"><path d="M3 2l10 11L3 24" fill="none" stroke="#999" stroke-width="2.5"/></svg>
</section>

<footer class="site-footer">
  <nav class="footer-nav">
    <a style="left:128px">Home</a>
    <a style="left:216px">About Us</a>
    <a style="left:325px">Services</a>
    <a style="left:426px">Training</a>
    <a style="left:525px">Join</a>
    <a style="left:593px">Contact</a>
  </nav>
  <div class="copyright">© 2016 Company Name &nbsp;All right reserved</div>
  <span class="social" style="left:902px" aria-label="Social link"></span>
  <span class="social" style="left:942px" aria-label="Social link"></span>
  <span class="social" style="left:982px" aria-label="Social link"></span>
  <span class="social" style="left:1021px" aria-label="Social link"></span>
</footer>

</body>
</html>
```